Business Card Re-Design/Update

We'd like to update out business cards. I've included our current "Style guide" which has the colour scheme of the organisation in it. I've also included the branding files with logos etc in them.

I've also included a copy of one of our existing cards so that you can see how ugly/dated they look. I'd like a fresh modern corporate look.

Target Market(s)

These are for our clients, potential clients, industry contacts - like all business cards

Contact Information for Business Card

Name
Position
Company Address - Level 1, 47 Fernby Street, Carlow Qld 4072
Direct Phone
mobile
Email
Website -www.korvalit.com.au
Logo

Colors

Designer to choose colors to be used in the design.

Requirements
Must have
• Main Logo
• Cards will need to be editable to be able to personalize them for each new employee.
Nice to have
• The MapOut, ShipWell, KeepSteady would be okay to have if they can be sensibly and professionally added to the look without detracting from the main imagery.
• Maybe they could go on the back of the card? will leave this to your creative discretion as to whether/where they fit.
Should not have
• Should not have decorative or script fonts

```html
<!DOCTYPE html>
<html lang="en">
<head>
<meta charset="utf-8">
<title>Korvalit Business Card</title>
<link rel="stylesheet" href="https://fonts.googleapis.com/css2?family=Roboto:wght@400;700&family=Roboto+Condensed:wght@700&display=swap">
<style>
  :root {
    --stage: #262626;
    --card-front: #f2f2f2;
    --card-back: #231f20;
    --brand-red: #c8161d;
    --brand-red-deep: #9e1016;
    --ink: #111111;
    --ink-soft: #555555;
    --white: #ffffff;
    --plan-green: #5a9e3a;
    --deliver-blue: #2386c8;
    --sustain-magenta: #b0248a;
  }
  * { box-sizing: border-box; margin: 0; padding: 0; }
  html, body { width: 1200px; height: 960px; overflow: hidden; }
  body {
    background: var(--stage);
    position: relative;
    font-family: "Roboto", Arial, sans-serif;
  }
  .card {
    position: absolute;
    width: 600px;
    height: 342px;
  }
  .card--front { left: 322px; top: 108px; background: var(--card-front); }
  .card--back { left: 320px; top: 493px; background: var(--card-back); }

  .person { position: absolute; left: 33px; top: 37px; }
  .person__name {
    font-family: "Roboto Condensed", "Arial Narrow", sans-serif;
    font-weight: 700;
    font-size: 21px;
    color: var(--brand-red);
    letter-spacing: 0.2px;
    line-height: 24px;
  }
  .person__role { font-size: 14px; color: var(--ink); line-height: 18px; }

  .address {
    position: absolute; left: 33px; top: 146px;
    font-size: 14.5px; line-height: 19px; color: var(--ink-soft);
    font-style: normal;
  }
  .contacts {
    position: absolute; left: 33px; top: 190px;
    list-style: none; font-size: 14.5px; line-height: 19px; color: var(--ink-soft);
  }
  .contacts li { display: flex; align-items: center; height: 19px; }
  .contacts svg { width: 12px; height: 12px; margin-right: 11px; fill: var(--brand-red); flex: none; }

  .brand-block {
    position: absolute; left: 302px; top: 50px;
    width: 240px; height: 240px;
    background: linear-gradient(180deg, var(--brand-red), var(--brand-red-deep));
  }

  .wordmark {
    position: absolute; left: 0; right: 0; top: 138px;
    display: flex; justify-content: center; align-items: center; gap: 22px;
  }
  .wordmark__square {
    width: 56px; height: 56px;
    background: var(--brand-red);
  }
  .wordmark__name {
    font-weight: 700; font-size: 52px; color: var(--white); letter-spacing: -1px;
  }

  .services {
    position: absolute; left: 46px; right: 46px; top: 275px;
    display: flex; justify-content: space-between; align-items: center;
  }
  .service { display: flex; align-items: center; gap: 8px; font-weight: 700; font-size: 26px; }
  .service__square { width: 20px; height: 20px; }
  .service--plan { color: var(--plan-green); }
  .service--plan .service__square { background: var(--plan-green); }
  .service--deliver { color: var(--deliver-blue); }
  .service--deliver .service__square { background: var(--deliver-blue); }
  .service--sustain { color: var(--sustain-magenta); }
  .service--sustain .service__square { background: var(--sustain-magenta); }
</style>
</head>
<body>

<section class="card card--front" aria-label="Card front">
  <div class="person">
    <p class="person__name">MAREN TALBOT</p>
    <p class="person__role">Business Development Manager</p>
  </div>
  <address class="address">Level 1, 47 Fernby Street<br>Carlow Qld 4072</address>
  <ul class="contacts">
    <li><svg viewBox="0 0 12 12"><path d="M2.5 0.5l2 2.2-1 1.3c0.7 1.6 2 2.9 3.5 3.6l1.3-1 2.2 2-1.2 2.4C4.6 10.6 1.4 7.4 0 2.3z"/></svg>+61 (0)7 3140 5521</li>
    <li><svg viewBox="0 0 12 12"><path d="M2.5 0.5l2 2.2-1 1.3c0.7 1.6 2 2.9 3.5 3.6l1.3-1 2.2 2-1.2 2.4C4.6 10.6 1.4 7.4 0 2.3z"/></svg>+61 (0)7 3140 5538</li>
    <li><svg viewBox="0 0 12 12"><path d="M3 0h6v12H3z M4.2 1.3v8h3.6v-8z"/></svg>+61 (0)412 604 287</li>
    <li><svg viewBox="0 0 12 12"><path d="M3 1h6v3H3z M0 5h12v5H0z M3 8h6v4H3z"/></svg>+61 (0)7 3140 5590</li>
    <li><svg viewBox="0 0 12 12"><path d="M0 2.5h12v7H0z M0.8 3.2L6 7l5.2-3.8" stroke="#f2f2f2" stroke-width="0.9"/></svg>mtalbot@korvalit.com.au</li>
    <li><svg viewBox="0 0 12 12"><circle cx="6" cy="6" r="6"/><path d="M3 4c1 0 2 1 1.5 2S5 8 4 9M7 2c0 1 1 1.5 2 1.5M8 7c1 0 1.5 1 1 2" stroke="#f2f2f2" stroke-width="1" fill="none"/></svg>www.korvalit.com.au</li>
  </ul>
  <div class="brand-block" aria-hidden="true"></div>
</section>

<section class="card card--back" aria-label="Card back">
  <div class="wordmark">
    <span class="wordmark__square" aria-hidden="true"></span>
    <span class="wordmark__name">korvalit</span>
  </div>
  <div class="services">
    <span class="service service--plan"><span class="service__square"></span>MapOut</span>
    <span class="service service--deliver"><span class="service__square"></span>ShipWell</span>
    <span class="service service--sustain"><span class="service__square"></span>KeepSteady</span>
  </div>
</section>

</body>
</html>
```